Tamsorellium we are a young innovative brand about making life easier for people with a disability

Our tag line is Making Life Easy, we are still a relatively new company trying to bring innovation and excitement into the disability space - with latest products and technology - we do have existing website but need to unpgrade for a stronger visual presence.

```html
<!DOCTYPE html>
<html lang="en">
<head>
<meta charset="utf-8">
<title>Tamsorellium – Making Life Easier</title>
<link href="https://fonts.googleapis.com/css2?family=Michroma&family=Lato:wght@400;700&family=Montserrat:wght@500;600;700&display=swap" rel="stylesheet">
<style>
:root{
  --red:#e00000;
  --red-dark:#b80000;
  --ink:#111111;
  --charcoal:#333333;
  --footer:#2f2f2f;
  --grey-tile:#9a9a9a;
  --hero-bg:#dfe0e8;
  --card-bg:#ececec;
  --white:#ffffff;
}
*{box-sizing:border-box;margin:0;padding:0}
html,body{width:1200px;height:2957px;overflow:hidden;background:var(--white)}
body{position:relative;font-family:'Lato',sans-serif;color:var(--ink)}
.abs{position:absolute}
.wide{font-family:'Michroma',sans-serif;white-space:nowrap}
.mont{font-family:'Montserrat',sans-serif}

/* promo bar */
.promo-bar{left:0;top:0;width:1200px;height:52px;background:var(--red);color:var(--white);display:flex;align-items:center;justify-content:center;font-family:'Montserrat',sans-serif;font-weight:700;font-size:13px;letter-spacing:1.6px;gap:22px}

/* header */
.brand{left:38px;top:78px;display:flex;align-items:center;gap:12px}
.brand-dot{width:74px;height:74px;border-radius:50%;background:var(--red)}
.brand-name{font-family:'Michroma',sans-serif;font-size:22px;color:var(--red)}
.search{left:471px;top:68px;width:467px;height:43px;border:1px solid #c9c9c9;display:flex}
.search span{flex:1;padding:12px 18px;color:#999;font-size:15px}
.search b{width:45px;background:var(--red);display:flex;align-items:center;justify-content:center}
.header-icons{left:970px;top:78px;display:flex;gap:30px}
.nav-line{left:427px;top:128px;width:773px;height:1px;background:#d5d5d5}
.nav-active{left:427px;top:128px;width:40px;height:3px;background:var(--red)}
.main-nav{top:148px;font-family:'Montserrat',sans-serif;font-size:13px;font-weight:500;letter-spacing:.8px}
.header-rule{left:0;top:180px;width:1200px;height:1px;background:#ddd}

/* hero */
.hero{left:0;top:181px;width:1200px;height:515px;background:var(--hero-bg)}
.hero-photo{left:600px;top:181px;width:600px;height:515px;background:linear-gradient(160deg,#d9dbe4 0%,#9fb7cc 45%,#3c4e78 100%)}
.hero-kicker{left:111px;top:277px;font-size:15px;letter-spacing:5px}
.hero-title{left:109px;top:316px;font-size:38px;color:var(--red);letter-spacing:3px}
.hero-tag{left:111px;top:378px;font-size:13px;letter-spacing:4px}
.hero-copy{left:111px;top:413px;width:420px;font-size:15px;line-height:29px;color:#222}
.pill{border-radius:30px;display:flex;align-items:center;justify-content:center;font-family:'Montserrat',sans-serif;font-weight:700;letter-spacing:1px;white-space:nowrap}
.hero-btn{left:111px;top:518px;width:146px;height:46px;background:var(--white);color:var(--red);font-size:15px;box-shadow:0 4px 8px rgba(0,0,0,.15)}
.dots{left:111px;top:606px;display:flex;gap:9px}
.dots i{width:8px;height:8px;border-radius:50%;background:#c9c9d2;display:block}
.dots i:first-child{background:var(--red)}

/* category tiles */
.tile{overflow:hidden}
.tile-label{color:var(--white);font-size:17px;line-height:29px}
.promo-panel{left:783px;top:760px;width:305px;height:471px;background:linear-gradient(135deg,var(--red) 0%,#d40000 45%,#c10000 100%);color:var(--white);text-align:center}
.promo-panel h2{font-family:'Michroma',sans-serif;font-weight:400;font-size:33px;line-height:56px;margin-top:26px;white-space:nowrap}
.promo-panel .upto{font-family:'Montserrat',sans-serif;font-style:italic;font-weight:700;font-size:21px;margin-top:12px}
.promo-panel .off{font-family:'Montserrat',sans-serif;font-weight:700;font-size:42px;margin-top:14px}
.promo-panel p{font-family:'Montserrat',sans-serif;font-size:14.5px;line-height:26px;padding:0 22px;margin-top:14px}
.promo-panel .panel-btn{margin:22px auto 0;width:136px;height:46px;border:2px solid var(--white);font-size:15px;font-weight:500;letter-spacing:0}

/* products */
.section-title{font-family:'Michroma',sans-serif;font-size:38px;letter-spacing:3px;white-space:nowrap}
.section-title em{font-style:normal;color:var(--red)}
.tab{top:1376px;height:48px;background:var(--charcoal);color:var(--white);font-size:15px}
.tab.is-active{background:var(--red)}
.product-card{top:1483px;width:295px;height:462px;background:var(--white);border-radius:14px;box-shadow:0 0 3px rgba(0,0,0,.25);border-bottom:8px solid var(--charcoal);text-align:center}
.product-photo{margin:0 auto;width:267px;height:320px;border-radius:0 0 14px 14px;background:var(--card-bg)}
.product-photo div{width:100%;height:100%;border-radius:14px}
.product-name{font-family:'Montserrat',sans-serif;font-weight:600;font-size:16px;line-height:30px;margin-top:30px;padding:0 24px}
.buy{display:inline-block;margin-top:6px;font-family:'Montserrat',sans-serif;font-weight:700;font-size:14px;color:var(--red);letter-spacing:1px;border-bottom:2px solid var(--red);line-height:16px}
.arrow{width:20px;height:20px;border-radius:50%;display:flex;align-items:center;justify-content:center}

/* about */
.about-mark{left:111px;top:2034px;width:388px;height:388px;border-radius:50%;border:34px solid var(--red);display:flex;align-items:center;justify-content:center}
.about-mark span{font-family:'Michroma',sans-serif;font-size:28px;color:var(--red)}
.about-title{left:588px;top:2032px;font-size:28px;letter-spacing:2px}
.about-copy{left:588px;top:2086px;width:500px;font-size:15px;line-height:29px;color:#333}
.about-btn{left:588px;top:2345px;width:146px;height:46px;background:var(--red);color:var(--white);font-size:14px;box-shadow:0 4px 8px rgba(0,0,0,.2)}

/* subscribe + footer */
.footer{left:0;top:2553px;width:1200px;height:404px;background:var(--footer)}
.subscribe{left:107px;top:2494px;width:980px;height:96px;background:var(--red);display:flex;align-items:center}
.subscribe h3{font-family:'Michroma',sans-serif;font-weight:400;font-size:20px;color:var(--white);margin-left:87px;width:366px;white-space:nowrap}
.sub-field{margin-left:0;width:442px;height:48px;background:var(--white);border-radius:24px;display:flex;align-items:center;justify-content:space-between;padding:0 4px 0 22px}
.sub-field span{font-size:12px;color:#666;letter-spacing:1px}
.sub-field b{background:var(--charcoal);color:var(--white);border-radius:22px;padding:11px 16px;font-family:'Montserrat',sans-serif;font-weight:500;font-size:15px;letter-spacing:1px}
.foot-col{top:2645px;color:var(--white)}
.foot-col h4{font-family:'Michroma',sans-serif;font-weight:400;font-size:17px;letter-spacing:1px;margin-bottom:22px;white-space:nowrap}
.foot-col li{list-style:none;font-size:15px;line-height:27.5px;display:flex;align-items:center;gap:8px}
.contact li{align-items:flex-start;margin-bottom:9px;line-height:20px}
.foot-brand{left:866px;top:2648px;display:flex;align-items:center;gap:10px;color:var(--white)}
.foot-brand i{width:50px;height:50px;border-radius:50%;background:var(--white);display:block}
.foot-brand span{font-family:'Michroma',sans-serif;font-size:17px}
.socials{left:880px;top:2722px;display:flex;gap:18px}
.socials i{width:21px;height:21px;border-radius:50%;background:var(--white);display:block}
.copyright{left:111px;top:2882px;width:973px;display:flex;align-items:center;gap:20px;color:var(--white);font-size:11px;font-weight:700}
.copyright hr{flex:1;border:none;border-top:1px solid #bbb}
</style>
</head>
<body>

<div class="abs promo-bar"><span>UP TO 75% OFF WEEKEND MEGA DEALS</span><span>|</span><span>SHOP NOW</span></div>

<header>
  <div class="abs brand"><i class="brand-dot"></i><span class="brand-name">Tamsorellium</span></div>
  <div class="abs search"><span>Search...</span><b><svg width="14" height="14" viewBox="0 0 14 14"><circle cx="6" cy="6" r="4.2" fill="none" stroke="#fff" stroke-width="2"/><line x1="9" y1="9" x2="12.5" y2="12.5" stroke="#fff" stroke-width="2"/></svg></b></div>
  <div class="abs header-icons">
    <svg width="20" height="20" viewBox="0 0 20 20"><circle cx="10" cy="6" r="4.5"/><path d="M2 20c0-5 3.5-8 8-8s8 3 8 8z"/></svg>
    <svg width="22" height="20" viewBox="0 0 22 20"><path d="M0 2h4l3 11h11l3-8H6" fill="none" stroke="#000" stroke-width="2.2"/><circle cx="9" cy="17" r="2"/><circle cx="17" cy="17" r="2"/><circle cx="19" cy="3" r="4" fill="#e00000"/></svg>
    <svg width="18" height="16" viewBox="0 0 18 16"><path d="M9 16 1.5 8.5A4.5 4.5 0 0 1 9 3a4.5 4.5 0 0 1 7.5 5.5z"/></svg>
  </div>
  <div class="abs nav-line"></div><div class="abs nav-active"></div>
  <nav>
    <span class="abs main-nav" style="left:428px;color:var(--red)">HOME</span>
    <span class="abs main-nav" style="left:533px">BARGAIN CENTER</span>
    <span class="abs main-nav" style="left:727px">PRODUCT</span>
    <span class="abs main-nav" style="left:862px">PARTS</span>
    <span class="abs main-nav" style="left:979px">ACCESSORIES</span>
  </nav>
  <div class="abs header-rule"></div>
</header>

<section>
  <div class="abs hero"></div>
  <div class="abs hero-photo" role="img" aria-label="Smiling man in a denim shirt seated in a manual wheelchair"></div>
  <div class="abs wide hero-kicker">WELCOME TO</div>
  <div class="abs wide hero-title">TAMSORELLIUM</div>
  <div class="abs wide hero-tag">MAKING LIFE EASIER</div>
  <p class="abs hero-copy">Are you trying to find the ideal wheelchair? Due to the vast number of possibilities, selecting a simple mobility item like a wheelchair can easily become overwhelming.</p>
  <div class="abs pill hero-btn">SHOP NOW</div>
  <div class="abs dots"><i></i><i></i><i></i><i></i></div>
</section>

<section>
  <div class="abs tile" style="left:111px;top:759px;width:399px;height:224px;background:linear-gradient(90deg,#6f6f6f,#b9b9b9)" role="img" aria-label="Handcycle attachment with 16 inch wheel and double-sided disc brakes"></div>
  <div class="abs tile" style="left:520px;top:759px;width:240px;height:224px;background:var(--grey-tile);text-align:center" role="img" aria-label="Grey wheelchair backpack">
    <p class="tile-label" style="margin-top:28px">Wheelchair/scooter<br>sports pac</p>
  </div>
  <div class="abs tile" style="left:111px;top:1008px;width:313px;height:224px;background:#e1e1e1" role="img" aria-label="Pair of black wheelchair push handles"></div>
  <div class="abs tile" style="left:446px;top:1008px;width:314px;height:224px;background:linear-gradient(120deg,#555,#2a2a2a)" role="img" aria-label="Close-up of a drive roller on a wheelchair tyre">
    <p class="tile-label" style="margin:62px 0 0 210px;font-size:16px;line-height:26px">Swift Glide<br>Roller<br>Repalcement<br>Kit</p>
  </div>
  <div class="abs promo-panel">
    <h2>NEW<br>ARRIVALS</h2>
    <div class="upto">Get Upto</div>
    <div class="off">40% OFF</div>
    <p>Tamsorellium offers wheelchairs for sale in various sizes, styles, price ranges, and combinations that meet a range of demands and requirements you need.</p>
    <div class="pill panel-btn">SHOP NOW</div>
  </div>
</section>

<section>
  <h2 class="abs section-title" style="left:0;width:1200px;top:1300px;text-align:center;font-weight:400">OUR <em>PRODUCT</em></h2>
  <div class="abs pill tab" style="left:205px;width:250px">POWER ASSIST UNITS</div>
  <div class="abs pill tab is-active" style="left:492px;width:111px">BAGS</div>
  <div class="abs pill tab" style="left:648px;width:348px">BRAKES/LOCKS &amp; COMPONENTS</div>

  <div class="abs arrow" style="left:43px;top:1690px;background:#888"><svg width="8" height="10" viewBox="0 0 8 10"><path d="M6 1 2 5l4 4" fill="none" stroke="#fff" stroke-width="2"/></svg></div>
  <div class="abs arrow" style="left:1125px;top:1690px;background:#000"><svg width="8" height="10" viewBox="0 0 8 10"><path d="M2 1l4 4-4 4" fill="none" stroke="#fff" stroke-width="2"/></svg></div>

  <article class="abs product-card" style="left:108px">
    <div class="product-photo"><div role="img" aria-label="Grey wheelchair sports backpack" style="background:linear-gradient(180deg,#e6e6e6,#cfcfcf)"></div></div>
    <p class="product-name">Tm1 - wheelchair/scooter sports pac</p>
    <span class="buy">BUY NOW</span>
  </article>
  <article class="abs product-card" style="left:452px">
    <div class="product-photo"><div role="img" aria-label="Black and grey compact backpack with red accents" style="background:linear-gradient(180deg,#e6e6e6,#cfcfcf)"></div></div>
    <p class="product-name">Ridgeline Trek - Compact - with adaptor</p>
    <span class="buy">BUY NOW</span>
  </article>
  <article class="abs product-card" style="left:793px">
    <div class="product-photo"><div role="img" aria-label="Black and grey compact backpack with red accents" style="background:linear-gradient(180deg,#e6e6e6,#cfcfcf)"></div></div>
    <p class="product-name">Ridgeline Trek - Compact - with adaptor</p>
    <span class="buy">BUY NOW</span>
  </article>
</section>

<section>
  <div class="abs about-mark"><span>Tamsorellium</span></div>
  <h2 class="abs section-title about-title" style="font-weight:400">ABOUT <em>TAMSORELLIUM</em></h2>
  <div class="abs about-copy">
    <p>Are you trying to find the ideal wheelchair? Due to the vast number of possibilities, selecting a simple mobility item like a wheelchair can easily become overwhelming.Tamsorellium offers wheelchairs for sale in various sizes, styles, price ranges, and combinations that meet a range of demands and requirements you need.</p>
    <p style="margin-top:29px">Everyone may find wheelchairs at Tamsorellium. We offer manual, power-assist units, and wheelchair accessories for sale and rental.</p>
  </div>
  <div class="abs pill about-btn">READ MORE</div>
</section>

<footer>
  <div class="abs footer"></div>
  <div class="abs subscribe">
    <h3>SUBSCRIBE FOR JOIN US</h3>
    <div class="sub-field"><span>Enter Your Email</span><b>SUBSCRIBE</b></div>
  </div>

  <div class="abs foot-col contact" style="left:109px">
    <h4>CONTACT US</h4>
    <ul>
      <li><svg width="12" height="16" viewBox="0 0 12 16"><path d="M6 0a6 6 0 0 1 6 6c0 4-6 10-6 10S0 10 0 6a6 6 0 0 1 6-6z" fill="#fff"/><circle cx="6" cy="6" r="2.2" fill="#2f2f2f"/></svg><span>Tamsorellium<br>United States</span></li>
      <li style="margin-top:6px"><svg width="14" height="14" viewBox="0 0 14 14"><path d="M3 0l3 3-2 2c1 2 3 4 5 5l2-2 3 3-2 3C6 14 0 8 0 3z" fill="#fff"/></svg><span>+1 555 014 2290</span></li>
      <li style="margin-top:6px"><svg width="13" height="10" viewBox="0 0 13 10"><rect width="13" height="10" fill="#fff"/><path d="M0 0l6.5 5L13 0" fill="none" stroke="#2f2f2f"/></svg><span>info@tamsorellium.com</span></li>
    </ul>
  </div>
  <div class="abs foot-col" style="left:414px">
    <h4>QUICK LINKS</h4>
    <ul><li>→ Home</li><li>→ About</li><li>→ Shop</li><li>→ Product</li><li>→ Contact Us</li></ul>
  </div>
  <div class="abs foot-col" style="left:657px">
    <h4>HELP CENTER</h4>
    <ul><li>→ FAQ</li><li>→ Warrently</li><li>→ Privacy Policy</li><li>→ Support Center</li><li>→ Terms &amp; Conditions</li></ul>
  </div>
  <div class="abs foot-brand"><i></i><span>Tamsorellium</span></div>
  <div class="abs socials"><i></i><i></i><i></i></div>

  <div class="abs copyright"><hr><span>Copyrights@2023.Tamsorellium .All Rights Reserved</span><hr></div>
</footer>

</body>
</html>
```